Need a clean & modern homepage for an education site + opportunity for longer term work

Thanks for viewing our project. We are excited about this new website and we hope that we might build a relationship with designers as we work on this project. I provided quite a few details and requirements to help you more quickly create a design that meets our needs.
Who we are:
We are a website that discusses the importance of college accreditation and provides a directory of college programs.
What we need:
A homepage that meets the below requirements and is inspired by the examples provided
Definition of accredited:
ac·cred·it·ed [uh-kred-i-tid] adj.
1. officially recognized as meeting the essential requirements, as of academic excellence: accredited schools.
2. provided with official credentials, as by a government: an accredited diplomatic representative.
3. accepted as authoritative: an accredited theory.
Overall look and feel for the homepage:
- Clean, simple and modern
- Limited (or zero) pictures
- Utilize color blocks with text
- A trend seems to be longer vertical length homepages with lots of whitespace. I generally like this trend as long as the page is not way to tall.
Inspirations: Sites that have a similar look and feel to what I need.
http://lernvoxa.org/
http://www.campusmetrik.com/colleges/brantmoor-university/
http://quietfolding.org/
http://www.velostrahiring.com/
http://www.zunq.com/
http://sketches.bxv.com/
Items to be included on the homepage. Details below on each item.
- Top navigation
- Logo: Please leave a blank area for a logo. The logo has not been designed.
- Simple graphic/color block at the top that highlights a definition of “Accredited” – the definition should be formatted like it is being copy/pasted from a dictionary.
- Space for a video and small (50 word) written description of the video. You can use placeholder text.
- One section with 3 Paragraphs of content (each paragraph around 100 words) with a header at the top. You can use placeholder text but please create the formatting. At the end of the 3 paragraphs please have a “Read More” Note this shouldn't be 3 separate paragraphs with three read mores - it is 3 paragraphs with one read more at the end.
- An area with the header “Search Colleges by State” that has anchor text links to all 50 states.
Top navigation:
- Home
- States – with a subnav dropdown that includes all 50 US states.
- Programs – with a subnav dropdown that includes program titles (list below)
- Degrees - with a subnav dropdown that includes 5 degree levels (list below)
- Accreditation – no subnav
- Rankings – no subnav
- Resources – no subnav
Footer
- Link to about us, privacy, and a copyright www.url.com
Programs List for sub navigation
Accounting
Art
Bible
Business
Criminal Justice
Design
Education
Engineering
English
Law
LPN to RN
Management
Math
MBA
MPH
Medical Assisting
Military
Nursing
Occupational Therapy
Paralegal
Psychology
Pharmacy
RN to BSN
Radiology
Social Work
Sonography
Degrees list for sub navigation
Certificate
Associate
Bachelors
Masters
PhD
Thanks so much - looking forward to working with you!
Education

```html
<!DOCTYPE html>
<html lang="en">
<head>
<meta charset="utf-8">
<title>Accredora – Homepage</title>
<link rel="stylesheet" href="https://fonts.googleapis.com/css2?family=Montserrat:wght@700;800&family=Figtree:ital,wght@0,400;0,600;1,400&display=swap">
<style>
  :root {
    --teal: #1aa285;
    --teal-dark: #0e6e5a;
    --teal-light: #7fe0c9;
    --navy: #2b3a4e;
    --paper: #eceff0;
    --white: #ffffff;
    --ink: #333b44;
    --mint: #c4ece0;
    --mint-fade: rgba(196, 236, 224, 0);
    --footer: #4a4a4a;
  }
  * { margin: 0; padding: 0; box-sizing: border-box; }
  html, body { width: 1200px; height: 2584px; overflow: hidden; }
  body { position: relative; background: var(--paper); font-family: "Figtree", sans-serif; color: var(--ink); }
  .backdrop { position: absolute; left: 0; top: 0; }
  .abs { position: absolute; }

  /* header */
  .logo { left: 140px; top: 36px; font-family: "Montserrat", sans-serif; font-weight: 800; font-size: 38px; line-height: 36px; color: var(--navy); letter-spacing: 1px; }
  .social { left: 960px; top: 40px; display: flex; gap: 9px; }
  .social span { width: 28px; height: 28px; display: block; }
  .social .s1 { background: var(--navy); }
  .social .s2 { background: var(--teal); }
  .social .s3 { background: #8a949e; }
  .main-nav { left: 326px; top: 92px; display: flex; gap: 24px; font-size: 16px; font-weight: 600; color: var(--navy); letter-spacing: .3px; }
  .main-nav .has-sub::after { content: "▾"; font-size: 10px; margin-left: 3px; }

  /* definition */
  .term { left: 169px; top: 184px; color: var(--white); }
  .term-label { font-size: 25px; font-weight: 600; letter-spacing: .5px; }
  .term-word { font-size: 39px; margin-top: 4px; line-height: 44px; }
  .term-say { font-size: 31px; font-style: italic; color: var(--teal-light); line-height: 36px; }
  .term-pos { font-size: 19px; font-style: italic; color: var(--teal-dark); margin-top: 4px; }
  .senses { left: 471px; top: 183px; width: 520px; list-style: none; color: var(--white); font-size: 18px; line-height: 22px; }
  .senses li { margin-bottom: 22px; }

  /* features */
  .feature { width: 300px; text-align: center; color: var(--white); }
  .feature svg { display: block; margin: 0 auto; }
  .feature h3 { font-family: "Montserrat", sans-serif; font-weight: 800; font-size: 26px; margin-top: 40px; letter-spacing: .5px; }
  .feature p { width: 262px; margin: 18px auto 0; font-size: 16px; line-height: 22px; color: #e3e8ee; }

  /* video */
  .video-copy { left: 140px; top: 902px; width: 330px; font-size: 16px; line-height: 27.6px; color: var(--ink); }
  .player { left: 545px; top: 859px; width: 517px; height: 343px; background: #3a3a3a; border-radius: 6px; padding: 6px; }
  .player-screen { width: 505px; height: 282px; background: linear-gradient(135deg, #6a5a4f, #8b6c5c 45%, #5d4436); }
  .play { left: 240px; top: 128px; width: 38px; height: 38px; background: var(--white); }
  .play::after { content: ""; position: absolute; left: 14px; top: 10px; border-left: 14px solid #333; border-top: 9px solid transparent; border-bottom: 9px solid transparent; }
  .track { left: 15px; top: 311px; width: 420px; height: 8px; background: #666; }
  .track-fill { width: 120px; height: 8px; background: var(--teal); }
  .knob { left: 132px; top: 304px; width: 10px; height: 22px; background: var(--white); }

  /* paragraphs */
  .section-title { left: 0; width: 1200px; text-align: center; font-family: "Montserrat", sans-serif; font-weight: 800; }
  .para-title { top: 1334px; font-size: 41px; color: var(--white); }
  .para { top: 1424px; width: 272px; text-align: center; font-size: 16px; line-height: 22.4px; color: var(--white); }
  .read-more { left: 514px; top: 1633px; width: 174px; height: 48px; border: 2px solid var(--teal); background: var(--white); color: var(--teal); font-family: "Montserrat", sans-serif; font-weight: 700; font-size: 16px; letter-spacing: 1.5px; display: flex; align-items: center; justify-content: center; }

  /* states */
  .state-map { left: 112px; top: 1784px; width: 976px; height: 630px; background: radial-gradient(ellipse 50% 50% at 50% 45%, var(--mint) 0%, var(--mint) 55%, var(--mint-fade) 100%); }
  .state-title { top: 1790px; font-size: 33px; color: var(--navy); letter-spacing: 1px; }
  .state-title em { font-family: "Figtree", sans-serif; font-style: italic; font-weight: 400; text-transform: none; }
  .state-col { top: 1903px; list-style: none; font-size: 16px; line-height: 33.2px; color: var(--ink); }

  /* footer */
  .footer-copy { left: 0; width: 1200px; top: 2495px; text-align: center; color: var(--white); font-size: 14px; font-weight: 600; letter-spacing: .3px; }
  .footer-links { left: 0; width: 1200px; top: 2530px; display: flex; justify-content: center; gap: 22px; color: var(--white); font-size: 13px; }
</style>
</head>
<body>

<svg class="backdrop" width="1200" height="2584" viewBox="0 0 1200 2584" aria-hidden="true">
  <rect x="0" y="0" width="1200" height="2584" fill="var(--paper)"/>
  <rect x="0" y="379" width="1200" height="423" fill="var(--navy)"/>
  <polygon points="0,147 1200,147 1200,379 600,428 0,379" fill="var(--teal)"/>
  <rect x="0" y="1245" width="1200" height="505" fill="var(--teal)"/>
  <ellipse cx="600" cy="1248" rx="790" ry="46" fill="var(--white)"/>
  <ellipse cx="600" cy="1746" rx="800" ry="66" fill="var(--white)"/>
  <polygon points="480,1664 720,1664 700,1704 500,1704" fill="var(--teal)"/>
  <polygon points="0,2483 200,2483 260,2436 940,2436 1000,2483 1200,2483 1200,2584 0,2584" fill="var(--footer)"/>
</svg>

<div class="state-map abs" role="img" aria-label="Map of the United States with state outlines"></div>

<header>
  <div class="logo abs">LOGO<br>HERE</div>
  <div class="social abs"><span class="s1"></span><span class="s2"></span><span class="s3"></span></div>
  <nav class="main-nav abs">
    <span>HOME</span><span class="has-sub">STATES</span><span class="has-sub">PROGRAMS</span><span class="has-sub">DEGREES</span><span>ACCREDITATION</span><span>RANKINGS</span><span>RESOURCES</span>
  </nav>
</header>

<section class="definition">
  <div class="term abs">
    <div class="term-label">“ACCREDITED”</div>
    <div class="term-word">ac·cred·it·ed</div>
    <div class="term-say">[uh-kred-i-tid]</div>
    <div class="term-pos">adjective</div>
  </div>
  <ol class="senses abs">
    <li>1. officially recognized as meeting the essential requirements, as of academic excellence: accredited schools.</li>
    <li>2. provided with official credentials, as by a government: an accredited diplomatic representative.</li>
    <li>3. accepted as authoritative: an accredited theory.</li>
  </ol>
</section>

<section class="features">
  <div class="feature abs" style="left:128px;top:466px">
    <svg width="84" height="78" viewBox="0 0 84 78" aria-hidden="true" fill="none" stroke="var(--teal)" stroke-width="5">
      <rect x="10" y="24" width="60" height="26" rx="13" transform="rotate(-35 40 37)"/>
      <circle cx="52" cy="52" r="8" fill="var(--teal)"/>
      <path d="M48,58 L44,74 M56,58 L62,74"/>
    </svg>
    <h3>RANKINGS</h3>
    <p>Egestas amet nullam dis. Ullamcorper netus cum accumsan pellentesque cubilia diam. A luctus turpis Rutrum fames quam integer. Etiam</p>
  </div>
  <div class="feature abs" style="left:450px;top:466px">
    <svg width="84" height="78" viewBox="0 0 84 78" aria-hidden="true" fill="var(--teal)">
      <polygon points="42,12 84,28 42,44 0,28"/>
      <path d="M20,38 L20,54 Q42,64 64,54 L64,38 L42,47 Z"/>
      <rect x="8" y="30" width="3" height="28"/>
      <rect x="5" y="56" width="9" height="12"/>
    </svg>
    <h3>ACCREDITATION</h3>
    <p>Massa commodo hendrerit blandit cras habitasse suspendisse eros pellentesque vel facilisis sodales, nulla volutpat conubia aliquet aptent eleifend commodo vitae hendrerit</p>
  </div>
  <div class="feature abs" style="left:774px;top:466px">
    <svg width="84" height="78" viewBox="0 0 84 78" aria-hidden="true" fill="var(--teal)">
      <polygon points="42,6 80,22 4,22"/>
      <rect x="6" y="24" width="72" height="6"/>
      <rect x="14" y="34" width="8" height="28"/><rect x="30" y="34" width="8" height="28"/>
      <rect x="46" y="34" width="8" height="28"/><rect x="62" y="34" width="8" height="28"/>
      <rect x="6" y="64" width="72" height="8"/>
    </svg>
    <h3>RESOURCES</h3>
    <p>Iaculis fermentum pellentesque sociosqu amet aenean netus, donec laoreet luctus. Accumsan nullam habitant felis Erat morbi taciti elit cubilia</p>
  </div>
</section>

<section class="video">
  <p class="video-copy abs">Quam praesent. Ullamcorper dolor primis natoque dolor. Erat mollis. Aliquam facilisis. Vestibulum pharetra natoque pulvinar nec. Praesent risus, morbi lobortis odio pretium aptent. Hendrerit ligula varius iaculis nonummy enim. Pulvinar mauris quam eleifend, iaculis vestibulum cras, dui nullam vulputate eu Ridiculus sit platea quis mi. Cubilia netus purus nunc etiam.</p>
  <div class="player abs">
    <div class="player-screen" role="img" aria-label="Video still of a study desk with books, notebooks and pencils"></div>
    <div class="play abs"></div>
    <div class="track abs"><div class="track-fill"></div></div>
    <div class="knob abs"></div>
    <svg class="abs" style="left:455px;top:306px" width="50" height="18" viewBox="0 0 50 18" aria-hidden="true" fill="#ddd">
      <polygon points="0,6 5,6 11,1 11,17 5,12 0,12"/>
      <path d="M14,5 Q18,9 14,13" stroke="#ddd" stroke-width="2" fill="none"/>
      <path d="M32,1 h6 M32,1 v6 M48,1 h-6 M48,1 v6 M32,17 h6 M32,17 v-6 M48,17 h-6 M48,17 v-6" stroke="#ddd" stroke-width="2"/>
    </svg>
  </div>
</section>

<section class="paragraphs">
  <h2 class="section-title para-title abs">PARAGRAPHS TITLE</h2>
  <p class="para abs" style="left:140px">Facilisi curae justo facilisis porta pede vivamus sem urna eget. Condimentum ad vel feugiat ad aliquam ornare taciti Lorem Suspendisse Congue quisque nostra lacinia, pharetra lacinia rhoncus venenatis nullam id montes suspendisse vehicula blandit tortor pellentesque sociis.</p>
  <p class="para abs" style="left:464px">Nullam rutrum parturient viverra netus dictum felis purus lacinia amet Senectus ante Penatibus augue molestie eros pretium mauris. Faucibus condimentum convallis. Blandit porta lorem ante et gravida litora mus.</p>
  <p class="para abs" style="left:790px">Velit litora, interdum augue, dapibus vel ornare condimentum quis dis dolor rutrum malesuada. Dapibus aptent orci mi non nibh quisque donec. Vestibulum litora arcu varius mus dapibus nascetur. Nonummy hendrerit sociis ullamcorper interdum.</p>
  <div class="read-more abs">READ MORE</div>
</section>

<section class="states">
  <h2 class="section-title state-title abs">SEARCH COLLEGES <em>by</em> STATE</h2>
  <ul class="state-col abs" style="left:167px"><li>Alabama</li><li>Alaska</li><li>Arizona</li><li>Arkansas</li><li>California</li><li>Colorado</li><li>Connecticut</li><li>Delaware</li><li>Florida</li><li>Georgia</li></ul>
  <ul class="state-col abs" style="left:360px"><li>Hawaii</li><li>Idaho</li><li>Illinois</li><li>Indiana</li><li>Iowa</li><li>Kansas</li><li>Kentucky</li><li>Louisiana</li><li>Maine</li><li>Maryland</li></ul>
  <ul class="state-col abs" style="left:536px"><li>Massachusetts</li><li>Michigan</li><li>Minnesota</li><li>Mississippi</li><li>Missouri</li><li>Montana</li><li>Nebraska</li><li>Nevada</li><li>New Hampshire</li><li>New Jersey</li></ul>
  <ul class="state-col abs" style="left:739px"><li>New Mexico</li><li>New York</li><li>North Carolina</li><li>North Dakota</li><li>Ohio</li><li>Oklahoma</li><li>Oregon</li><li>Pennsylvania</li><li>Rhode Island</li><li>South Carolina</li></ul>
  <ul class="state-col abs" style="left:933px"><li>South Dakota</li><li>Tennessee</li><li>Texas</li><li>Utah</li><li>Vermont</li><li>Virginia</li><li>Washington</li><li>West Virginia</li><li>Wisconsin</li><li>Wyoming</li></ul>
</section>

<footer>
  <p class="footer-copy abs">COPYRIGHT © 2013 WWW.ACCREDORA.COM. ALL RIGHTS RESERVED.</p>
  <nav class="footer-links abs"><span>ABOUT US</span><span>PRIVACY</span></nav>
</footer>

</body>
</html>
```